Business Card Design

It's an investment advisory service for individuals with all there investment needs. Also financial consulting to businesses and governmental agencies on retirement plans etc. It's personalized not commoditized help. Should show strength, knowledge and money orientation.

Reason: Will be out of town setting up office.

Reason: waiting for the 2/3rds of group to vote

Reason: only half the votes are in, I'm calling and getting verbals, but at this time we are down to 2 designs.

Industry/Entity Type

Investment

Contact Information for Business Card

B. Rel K. Financial Consulting and Wealth Management, Berislav Mike Holcek, 5172 Pasadena Loma Verde, San Diego, CA 94417-6381, Registered Investment Advisor

Requirements
Nice to have
• Something money oriented

```html
<!DOCTYPE html>
<html lang="en">
<head>
<meta charset="utf-8">
<title>B. Rel K. Business Cards</title>
<link href="https://fonts.googleapis.com/css2?family=Crimson+Text:wght@400;600&display=swap" rel="stylesheet">
<style>
  :root {
    --backdrop: #1d1d1d;
    --brand-green: #3d773c;
    --deep-green: #2f6a31;
    --band-green: #3b7b3c;
    --paper: #ffffff;
    --bill-tint: #dfe6db;
    --bill-shade: #c9d3c3;
    --ink: #222222;
  }
  * { margin: 0; padding: 0; box-sizing: border-box; }
  html, body { width: 1200px; height: 1000px; overflow: hidden; }
  body {
    background: var(--backdrop);
    position: relative;
    font-family: "Crimson Text", Georgia, serif;
  }
  .card {
    position: absolute;
    width: 750px;
    height: 431px;
    overflow: hidden;
    background: var(--paper);
  }
  .card--centered { left: 231px; top: 51px; }
  .card--offset { left: 233px; top: 500px; height: 430px; width: 748px; }

  .money-backdrop {
    position: absolute;
    inset: 0;
    background:
      linear-gradient(to right, rgba(88,140,80,0.55) 0, rgba(88,140,80,0) 34px, rgba(88,140,80,0) calc(100% - 34px), rgba(88,140,80,0.55) 100%),
      linear-gradient(to bottom, var(--bill-shade) 0%, var(--bill-tint) 30%, #eef1ec 52%, var(--paper) 66%, var(--paper) 72%, #9dbf98 86%, var(--band-green) 94%, var(--deep-green) 100%);
  }
  .card--offset .money-backdrop {
    background:
      linear-gradient(to right, rgba(88,140,80,0.55) 0, rgba(88,140,80,0) 34px, rgba(88,140,80,0) calc(100% - 34px), rgba(88,140,80,0.55) 100%),
      linear-gradient(to bottom, #f2f4f0 0%, var(--bill-tint) 22%, #e9ede6 45%, var(--paper) 62%, var(--paper) 70%, #9dbf98 85%, var(--band-green) 93%, var(--deep-green) 100%);
  }

  .brand-block {
    position: absolute;
    background: var(--brand-green);
    color: var(--paper);
    display: flex;
    flex-direction: column;
    align-items: center;
    justify-content: center;
    text-align: center;
    font-weight: 400;
  }
  .card--centered .brand-block { left: 280px; top: 0; width: 198px; height: 187px; }
  .card--offset .brand-block { left: 0; top: 91px; width: 243px; height: 230px; }
  .brand-name { font-size: 44px; line-height: 1; letter-spacing: 1px; }
  .card--offset .brand-name { font-size: 54px; }
  .brand-tagline { margin-top: 14px; font-size: 13px; line-height: 1.2; text-transform: uppercase; letter-spacing: 0.3px; }
  .card--offset .brand-tagline { font-size: 15.5px; margin-top: 18px; }

  .contact {
    position: absolute;
    line-height: 1;
  }
  .card--centered .contact { left: 0; right: 0; top: 210px; text-align: center; padding-left: 0; }
  .card--offset .contact { right: 67px; top: 158px; text-align: right; }

  .person-name { font-weight: 600; font-size: 31px; color: var(--brand-green); }
  .card--offset .person-name { color: var(--ink); }
  .credentials { font-size: 19px; color: var(--brand-green); margin-top: 9px; }
  .credentials sup { font-size: 11px; }
  .phone-line { font-size: 25px; color: var(--ink); margin-top: 26px; display: flex; align-items: center; gap: 6px; justify-content: center; }
  .card--offset .phone-line { justify-content: flex-end; color: var(--brand-green); margin-top: 46px; }
  .phone-icon { width: 21px; height: 21px; }
  .email { font-size: 25px; color: var(--ink); margin-top: 7px; }
  .card--offset .email { color: var(--brand-green); margin-top: 9px; }

  .role-title {
    position: absolute;
    left: 0; right: 0;
    bottom: 24px;
    text-align: center;
    color: var(--paper);
    font-size: 20px;
    letter-spacing: 6.2px;
    text-transform: uppercase;
  }
  .card--offset .role-title { bottom: 24px; }
</style>
</head>
<body>

  <section class="card card--centered">
    <div class="money-backdrop" role="img" aria-label="Soft green-tinted photograph of fanned hundred-dollar bills"></div>
    <div class="brand-block">
      <div class="brand-name">B. Rel K.</div>
      <div class="brand-tagline">Financial Consulting<br>&amp; Wealth Management</div>
    </div>
    <div class="contact">
      <div class="person-name">Berislav “Mike” Holcek</div>
      <div class="credentials">MBA, RP<sup>©</sup>, CRC<sup>©</sup></div>
      <div class="phone-line">
        <svg class="phone-icon" viewBox="0 0 24 24" aria-hidden="true">
          <circle cx="12" cy="12" r="10.5" fill="none" stroke="var(--brand-green)" stroke-width="1.6"/>
          <path d="M9 6.5c-1.2.6-2 2-1.6 3.8.6 2.7 2.6 5.6 5 7 1.5.9 3 .8 3.9-.2l-1.8-2.2-1.6.7c-1.2-.8-2.3-2.3-2.8-3.7l1.3-1.1L9 6.5z" fill="var(--brand-green)"/>
        </svg>
        <span>858-314-7092 / 775-608-2153</span>
      </div>
      <div class="email">mike.holcek@relkmail.com</div>
    </div>
    <div class="role-title">Registered Investment Advisor</div>
  </section>

  <section class="card card--offset">
    <div class="money-backdrop" role="img" aria-label="Soft green-tinted photograph of fanned hundred-dollar bills"></div>
    <div class="brand-block">
      <div class="brand-name">B. Rel K.</div>
      <div class="brand-tagline">Financial Consulting<br>&amp; Wealth Management</div>
    </div>
    <div class="contact">
      <div class="person-name">Berislav “Mike” Holcek</div>
      <div class="credentials">MBA, RP<sup>©</sup>, CRC<sup>©</sup></div>
      <div class="phone-line">
        <svg class="phone-icon" viewBox="0 0 24 24" aria-hidden="true">
          <circle cx="12" cy="12" r="10.5" fill="none" stroke="var(--brand-green)" stroke-width="1.6"/>
          <path d="M9 6.5c-1.2.6-2 2-1.6 3.8.6 2.7 2.6 5.6 5 7 1.5.9 3 .8 3.9-.2l-1.8-2.2-1.6.7c-1.2-.8-2.3-2.3-2.8-3.7l1.3-1.1L9 6.5z" fill="var(--brand-green)"/>
        </svg>
        <span>858-314-7092 / 775-608-2153</span>
      </div>
      <div class="email">mike.holcek@relkmail.com</div>
    </div>
    <div class="role-title">Registered Investment Advisor</div>
  </section>

</body>
</html>
```